A clean crisp business card for a Landscape Construction company. Designed to be easy to read contact/ info and also be appealing/interesting, unlike a traditional business card.

Industry/Entity Type

Landscape Construction

Contact Information for Business Card

Company name : Brambleford Landscape Construction, phone number: (877) 62Vista, website:Bramblefordyards.example, Email, sales@bramblefordyards.example

Requirements
Nice to have
• Luxurious finishes/ details…. Icons or emblems next to contact info
Should not have
• Clipart or general pictures

```html
<!DOCTYPE html>
<html lang="en">
<head>
<meta charset="utf-8">
<title>Brambleford Landscape Construction – Business Card</title>
<link rel="stylesheet" href="https://fonts.googleapis.com/css2?family=Cinzel:wght@600&family=Arimo:wght@400&display=swap">
<style>
  :root {
    --bg-top: #d2d2d2;
    --bg-bottom: #9c9c9c;
    --brand-blue: #1f6bb5;
    --leaf-green: #95c83d;
    --paper: #ffffff;
    --serif: "Cinzel", Georgia, serif;
    --sans: "Arimo", Arial, sans-serif;
  }
  * { box-sizing: border-box; margin: 0; padding: 0; }
  html, body { width: 1200px; height: 788px; overflow: hidden; }
  body {
    background: linear-gradient(180deg, var(--bg-top), var(--bg-bottom));
    position: relative;
  }
  .card {
    position: absolute;
    top: 240px;
    width: 540px;
    height: 309px;
    border-radius: 22px;
    overflow: hidden;
    box-shadow: 0 14px 30px rgba(0,0,0,0.35);
  }
  .card--front { left: 40px; background: var(--paper); }
  .card--back { left: 620px; background: var(--brand-blue); }

  .card__wave { position: absolute; inset: 0; width: 100%; height: 100%; }

  .brand-name {
    position: absolute;
    font-family: var(--serif);
    font-weight: 600;
    line-height: 1.15;
  }
  .card--front .brand-name {
    left: 34px; top: 96px;
    color: var(--brand-blue);
    font-size: 22px;
  }
  .card--front .brand-name small { display: block; font-size: 12px; letter-spacing: 2px; }
  .card--back .brand-name {
    left: 0; right: 0; top: 112px;
    text-align: center;
    color: var(--paper);
    font-size: 46px;
  }
  .card--back .brand-name small { display: block; font-size: 18px; letter-spacing: 6px; margin-top: 6px; }

  .contact-list {
    position: absolute;
    left: 292px; top: 176px;
    list-style: none;
    font-family: var(--sans);
    font-size: 13px;
    color: var(--paper);
  }
  .contact-list li { display: flex; align-items: center; gap: 8px; margin-bottom: 9px; }
  .contact-list svg { width: 13px; height: 13px; fill: var(--leaf-green); flex: none; }

  .person {
    position: absolute;
    left: 34px; bottom: 22px;
  }
  .person__name {
    font-family: var(--serif);
    font-weight: 600;
    font-size: 22px;
    color: var(--leaf-green);
  }
  .person__role {
    font-family: var(--sans);
    font-size: 15px;
    color: var(--paper);
  }
</style>
</head>
<body>

<section class="card card--front" aria-label="Business card front">
  <svg class="card__wave" viewBox="0 0 540 309" preserveAspectRatio="none" aria-hidden="true">
    <path d="M0,232 C150,232 250,190 330,120 C400,58 470,42 540,44 L540,309 L0,309 Z" fill="var(--brand-blue)"/>
    <path d="M0,225 C150,225 250,183 330,113 C400,51 470,35 540,37" fill="none" stroke="var(--leaf-green)" stroke-width="4"/>
  </svg>

  <div class="brand-name">Brambleford<small>Landscape Construction</small></div>

  <ul class="contact-list">
    <li>
      <svg viewBox="0 0 24 24" aria-hidden="true"><path d="M6.6 10.8a15.1 15.1 0 0 0 6.6 6.6l2.2-2.2a1 1 0 0 1 1-.25 11.4 11.4 0 0 0 3.6.57 1 1 0 0 1 1 1V20a1 1 0 0 1-1 1A17 17 0 0 1 3 4a1 1 0 0 1 1-1h3.5a1 1 0 0 1 1 1c0 1.25.2 2.45.57 3.57a1 1 0 0 1-.25 1z"/></svg>
      (877) 62Vista
    </li>
    <li>
      <svg viewBox="0 0 24 24" aria-hidden="true"><path d="M2 5h20v14H2zm2 2v.5l8 5 8-5V7l-8 5z"/></svg>
      sales@bramblefordyards.example
    </li>
    <li>
      <svg viewBox="0 0 24 24" aria-hidden="true"><circle cx="12" cy="12" r="10"/></svg>
      bramblefordyards.example
    </li>
  </ul>

  <div class="person">
    <div class="person__name">Owen Hartley</div>
    <div class="person__role">Founder</div>
  </div>
</section>

<section class="card card--back" aria-label="Business card back">
  <div class="brand-name">Brambleford<small>Landscape Construction</small></div>
</section>

</body>
</html>
```